English and Spanish Language School Needs a Business Card

Need a business card design a startup company called Maribel Language School. The company will offer English and Spanish conversational level courses designed to make the learner feel comfortable with grammar and vocabulary. We would like to see a logo with some colour that should communicate learning, growth.

Target Market(s)

Consumers and businesses

Industry/Entity Type

Education

Contact Information for Business Card

TBD

Font styles to use
Serif

Requirements
Must have
• Include the following
• Logo
• Name
• Title
• Cellphone Number
• Office Phone number
• Email address
• Office Address

```html
<!DOCTYPE html>
<html lang="en">
<head>
<meta charset="utf-8">
<title>Maribel Language School – Business Card</title>
<link href="https://fonts.googleapis.com/css2?family=Montserrat:wght@400;500;700&display=swap" rel="stylesheet">
<style>
  :root {
    --backdrop: #2b2b2d;
    --card: #050505;
    --red: #d4212b;
    --cyan: #13a3ad;
  }
  * { margin: 0; padding: 0; box-sizing: border-box; }
  html, body { width: 1200px; height: 900px; overflow: hidden; }
  body {
    background: var(--backdrop);
    font-family: "Montserrat", Arial, sans-serif;
    position: relative;
  }
  .card {
    position: absolute;
    width: 620px;
    height: 354px;
    background: var(--card);
    border-radius: 22px;
    box-shadow: 0 14px 30px rgba(0,0,0,.45);
  }
  .card--front { left: 110px; top: 80px; }
  .card--back  { left: 470px; top: 470px; }

  .wordmark { color: var(--red); font-weight: 700; line-height: 1; }
  .wordmark__name { display: block; letter-spacing: -1px; }
  .wordmark__sub  { display: block; letter-spacing: .5px; margin-top: 6px; }

  .card--front .wordmark {
    position: absolute; left: 0; right: 0; top: 100px; text-align: center;
  }
  .card--front .wordmark__name { font-size: 82px; }
  .card--front .wordmark__sub  { font-size: 24px; }

  .website {
    position: absolute; left: 0; right: 0; bottom: 44px;
    text-align: center; font-size: 17px; font-weight: 500;
    color: var(--cyan); letter-spacing: .3px;
  }
  .website .accent { color: var(--red); }

  .card--back .wordmark {
    position: absolute; left: 34px; top: 138px; width: 250px;
  }
  .card--back .wordmark__name { font-size: 54px; }
  .card--back .wordmark__sub  { font-size: 17px; }

  .divider {
    position: absolute; left: 300px; top: 54px; bottom: 54px;
    width: 2px; background: var(--cyan);
  }
  .contact {
    position: absolute; left: 324px; top: 56px; right: 20px;
    color: var(--cyan); font-size: 14px; line-height: 1.45;
  }
  .contact__name { color: var(--red); font-size: 22px; font-weight: 700; letter-spacing: .5px; }
  .contact__title { margin-bottom: 12px; }
  .contact__address { margin-bottom: 12px; }
  .contact__list { list-style: none; }
  .contact__list li { display: flex; align-items: center; gap: 8px; }
  .contact__list svg { width: 12px; height: 12px; flex: none; }
  .contact__list .web { color: var(--red); font-weight: 700; }
  .icon-red { stroke: var(--red); fill: none; stroke-width: 2; }
</style>
</head>
<body>

<section class="card card--front">
  <div class="wordmark">
    <span class="wordmark__name">Maribel</span>
    <span class="wordmark__sub">Language School</span>
  </div>
  <p class="website"><span class="accent">www.</span>maribellanguageschool<span class="accent">.com</span></p>
</section>

<section class="card card--back">
  <div class="wordmark">
    <span class="wordmark__name">Maribel</span>
    <span class="wordmark__sub">Language School</span>
  </div>
  <div class="divider"></div>
  <div class="contact">
    <p class="contact__name">Daniel Harper</p>
    <p class="contact__title">Director</p>
    <p class="contact__address">Po Box 218<br>Ashford VIC 3920</p>
    <ul class="contact__list">
      <li><svg viewBox="0 0 12 12"><rect class="icon-red" x="3" y="1" width="6" height="10" rx="1"/></svg>+330 2715-4482</li>
      <li><svg viewBox="0 0 12 12"><path class="icon-red" d="M2 1.5l2.5 0 1 2.5-1.5 1a6 6 0 0 0 3 3l1-1.5 2.5 1v2.5A9 9 0 0 1 2 1.5z"/></svg>+330 2389-6127</li>
      <li><svg viewBox="0 0 12 12"><rect class="icon-red" x="1" y="2.5" width="10" height="7"/><path class="icon-red" d="M1 2.5l5 4 5-4"/></svg>hello@maribelschool.com</li>
      <li class="web"><svg viewBox="0 0 12 12"><circle class="icon-red" cx="6" cy="6" r="4.8"/><path class="icon-red" d="M1.2 6h9.6M6 1.2c-2.5 3-2.5 6.6 0 9.6M6 1.2c2.5 3 2.5 6.6 0 9.6"/></svg>maribellanguageschool.com</li>
    </ul>
  </div>
</section>

</body>
</html>
```